Business Card Design for Flood Rescue 360 - Property Restoration Professionals

I need a business card designed for Flood Rescue 360. We are a full-service property restoration solution. Providing water, fire, smoke & storm restoration as well as mold remediation and full remodel or reconstruction to homes and businesses across Tulsa Metro, OK.
Target Market(s)
home and business owners with insurance covered property damage from water, fire or storm related damage
Industry/Entity Type
property restoration
Contact Information for Business Card
Marcus Pelley General Manager Cell: 214-555-0193 Office: 469-555-0148 email: Marcus@FloodRescue360.example services: Water, Fire, Mold, Reconstruction Tagline: Fast Help When the Water Rises!
Look and feel
Each slider illustrates characteristics of the customer's brand and the style your logo design should communicate.

```html
<!DOCTYPE html>
<html lang="en">
<head>
<meta charset="utf-8">
<title>Flood Rescue 360 – Business Card</title>
<link rel="stylesheet" href="https://fonts.googleapis.com/css2?family=Exo+2:wght@600&family=Montserrat:wght@400;600;700&family=Roboto:wght@900&display=swap">
<style>
  :root {
    --brand-blue: #00afe3;
    --brand-deep: #0d6f96;
    --ink: #1d1d1f;
    --paper: #ffffff;
    --backdrop: #e4e2e3;
  }
  * { margin: 0; padding: 0; box-sizing: border-box; }
  html, body { width: 1200px; height: 1108px; overflow: hidden; }
  body { background: var(--backdrop); position: relative; font-family: "Montserrat", sans-serif; color: var(--ink); }

  .card { position: absolute; width: 767px; overflow: hidden; }
  .card--front { left: 232px; top: 57px; height: 468px; background: var(--paper); }
  .card--back { left: 231px; top: 584px; height: 450px; background: var(--brand-blue); }

  .brand { position: absolute; display: flex; align-items: center; }
  .brand__name {
    font-family: "Roboto", sans-serif; font-weight: 900; line-height: 0.86;
    text-transform: uppercase; letter-spacing: -1px; white-space: nowrap;
  }
  .card--front .brand { right: 42px; top: 66px; gap: 14px; }
  .card--front .brand__name { color: var(--brand-blue); font-size: 60px; text-align: right; }
  .card--back .brand { left: 50%; transform: translateX(-50%); top: 142px; gap: 22px; }
  .card--back .brand__name { color: var(--brand-deep); font-size: 76px; text-align: left; }

  .person { position: absolute; left: 23px; top: 249px; }
  .person__name { font-family: "Exo 2", sans-serif; font-weight: 600; font-size: 31px; color: var(--brand-blue); line-height: 1; }
  .person__title { font-size: 18px; margin-top: 6px; }

  .divider { position: absolute; left: 23px; right: 41px; top: 313px; height: 2px; background: var(--brand-blue); }

  .contacts { position: absolute; left: 25px; top: 331px; list-style: none; }
  .contacts li { display: flex; align-items: center; gap: 10px; font-size: 18px; height: 28px; }
  .contacts svg { width: 18px; height: 18px; fill: var(--brand-blue); }

  .region { position: absolute; right: 39px; top: 385px; font-size: 18px; }

  .services {
    position: absolute; left: 0; right: 0; bottom: 0; height: 39px; background: var(--brand-blue);
    color: var(--paper); font-weight: 600; font-size: 18px; display: flex; align-items: center; justify-content: center;
  }

  .tagline {
    position: absolute; left: 0; right: 0; top: 376px; text-align: center;
    color: var(--paper); font-weight: 700; font-size: 17px;
  }
</style>
</head>
<body>
  <section class="card card--front">
    <div class="brand">
      <div class="brand__name">Flood<br>Rescue 360</div>
      <svg width="112" height="112" viewBox="0 0 112 112" aria-hidden="true"><circle cx="56" cy="56" r="50" fill="none" stroke="#00afe3" stroke-width="8"/></svg>
    </div>

    <div class="person">
      <h1 class="person__name">Marcus Pelley</h1>
      <p class="person__title">General Manager</p>
    </div>
    <div class="divider"></div>

    <ul class="contacts">
      <li><svg viewBox="0 0 24 24" aria-hidden="true"><path d="M6.6 10.8a15.2 15.2 0 0 0 6.6 6.6l2.2-2.2a1 1 0 0 1 1-.25 11.4 11.4 0 0 0 3.6.57 1 1 0 0 1 1 1V20a1 1 0 0 1-1 1A17 17 0 0 1 3 4a1 1 0 0 1 1-1h3.5a1 1 0 0 1 1 1c0 1.25.2 2.45.57 3.57a1 1 0 0 1-.25 1z"/></svg>214-555-0193</li>
      <li><svg viewBox="0 0 24 24" aria-hidden="true"><path d="M2 8c0-3 20-3 20 0v2h-5V8H7v2H2zM6 11h12l3 9H3zm6 2.5a2.5 2.5 0 1 0 0 5 2.5 2.5 0 0 0 0-5z"/></svg>469-555-0148</li>
      <li><svg viewBox="0 0 24 24" aria-hidden="true"><path d="M2 5h20v2l-10 6L2 7zm0 4l10 6 10-6v10H2z"/></svg>Marcus@FloodRescue360.example</li>
    </ul>
    <p class="region">Tulsa Metro, OK.</p>

    <div class="services">• Water • Fire • Mold • Reconstruction</div>
  </section>

  <section class="card card--back">
    <div class="brand">
      <div class="brand__name">Flood<br>Rescue 360</div>
      <svg width="150" height="150" viewBox="0 0 150 150" aria-hidden="true"><circle cx="75" cy="75" r="68" fill="none" stroke="#0d6f96" stroke-width="8"/></svg>
    </div>
    <p class="tagline">Fast Help When the Water Rises!</p>
  </section>
</body>
</html>
```